Bluefern Business Services needs a new interactive and interesting website

We need an interesting, professional, modern and functional company website for Bluefern Business Services - a young IT Services company based out of Chennai, India.

Bluefern Business Services is a fully owned subsidiary of Marlow Goods, one of the world's leading direct to consumer wine merchant.

We already have a registered company logo which must feature in the website.

We conceive, design, develop, test, implement and support IT solutions across the entire Marlow Goods IT landscape. For ex : We currently run about 25 e-commerce websites for Marlow Goods on ATG and Dot Net.

We would like to see our corporate colors used in the website. (Burgundy wine and wine green - source: www.bluefernbs-site.com)

We are looking at this website to communicate a fun, friendly and professionally managed company - reaching out to career seekers, prospective customers and general public.

For reference - The company name 'Bluefern' is an inspiration from the Marlow Goods lineage.

The second image with the world map is stickered on our main entrance to the office, I am not sure where this can be used -just putting it out there..

Please note that there are only a few more days to submit designs for this contest  !

I would appreciate if you can help posting your designs in time for our review and consideration.

Thanks.

Reason: Thanks for your inputs. We have a number of designers and a lot to digest and work with in the past few days. There has been a rush of new designs in the last few days Hence we will require more time to process these and make our decision. Hence i am requesting the contest to be open for more days. Regards, Tarun

Target Market(s)

Prospective job seekers who want to know more about the company and also wish to apply for a job vacancy
People wanting to know more about the company in general and our progress
People who want to see what we offer and how we can help them too - prospective customers
Companies that are interested in our IT Captive journey and are looking for a business opportunity

Industry/Entity Type

E-Commerce

Requirements
Must have
• Log In/ Register facility acting as a Single Sign on for Intranet (Employees)

Facility to post job vacancies (with an expiry date) and enable people to apply for a role and upload their CV/Resume.

Facility to Review Job applications

Facility for website visitors to contact Bluefern business Services via an online 'Contact Us' form with a split of job seekers and business opportunities

Gallery facility to upload pictures regarding company events
Nice to have
• Less Cluttered and contemporary design
Some Wine/Vineyard inspirations will be good but not too much, the company is an IT services company

```html
<!DOCTYPE html>
<html lang="en">
<head>
<meta charset="utf-8">
<title>Bluefern Business Services</title>
<link href="https://fonts.googleapis.com/css2?family=Open+Sans:wght@400;600&display=swap" rel="stylesheet">
<style>
:root{
  --burgundy:#8a1538;
  --green:#7a8c2c;
  --ink:#333;
  --muted:#8a8a8a;
  --card:#efefef;
  --dark:#2b2b2b;
  --darker:#1c1c1c;
  --panel:#232323;
}
*{box-sizing:border-box;margin:0;padding:0}
html,body{width:781px;height:1200px;overflow:hidden;background:#fff}
body{font-family:'Open Sans',Arial,sans-serif;color:var(--ink);position:relative}
.site-header{position:absolute;top:0;left:0;width:781px;height:62px;border-top:2px solid #111;background:#fff}
.brand{position:absolute;left:76px;top:12px;display:flex;align-items:center;gap:7px;color:var(--burgundy);font-weight:600}
.brand-dot{width:16px;height:16px;border-radius:50%;background:var(--burgundy)}
.brand-name{font-size:20px;line-height:20px;display:block}
.brand-sub{font-size:12.5px;line-height:15px;display:block;font-weight:400}
.main-nav{position:absolute;top:25px;left:330px;display:flex;font-size:10.5px}
.main-nav a{color:#333;text-decoration:none;margin-right:26px}
.main-nav a.active{color:var(--burgundy);font-weight:600}
.hero{position:absolute;top:62px;left:0;width:781px;height:309px;background:linear-gradient(90deg,#e9d3c2 0%,#d8b9a0 35%,#8d7a6a 60%,#b39a86 80%,#6e5a4c 100%)}
.hero-caption{position:absolute;left:74px;top:124px;width:235px;height:113px;background:rgba(60,60,60,.85);border-left:3px solid var(--green);padding:9px 12px 0 13px;color:#fff}
.hero-caption h1{font-weight:400;font-size:15.5px;margin-bottom:6px}
.hero-caption p{font-size:9px;line-height:11px;color:#e8e8e8}
.job-search{position:absolute;left:72px;top:362px;width:637px;height:76px;background:var(--panel);border-radius:2px}
.field{position:absolute;top:16px;color:#fff;font-size:10px}
.field .box{margin-top:4px;height:28px;background:#fff;border-radius:2px;display:flex;align-items:center;padding-left:6px;gap:6px;color:#bbb;font-size:9px}
.search-btn{position:absolute;left:563px;top:33px;width:66px;height:25px;background:var(--green);border-radius:3px;color:#fff;font-size:10px;display:flex;align-items:center;gap:8px;padding-left:6px;box-shadow:0 2px 0 #4f5c1c}
.services{position:absolute;top:470px;left:0;width:781px}
.service{position:absolute;top:43px;height:151px;width:135px;background:var(--card);border:1px solid #ddd;text-align:center;padding:15px 10px 0;box-shadow:0 6px 8px -6px rgba(0,0,0,.25)}
.service-icon{position:absolute;top:-43px;left:39px;width:56px;height:56px;border-radius:50%;background:#fff;border:1px solid #a4ae72;display:flex;align-items:center;justify-content:center}
.service h2{font-weight:400;font-size:10px;color:#555;line-height:12px;margin:0 -8px}
.service p{font-size:7.5px;line-height:10.7px;color:var(--muted);margin-top:16px}
.service.two-line p{margin-top:14px}
.service .read-more{position:absolute;bottom:6px;left:43px;width:49px;height:14px;background:var(--green);color:#fff;font-size:7.5px;line-height:14px;border-radius:1px}
.gallery-title{position:absolute;left:80px;top:707px;font-size:14px;font-weight:400;color:#333}
.upload-link{position:absolute;left:633px;top:707px;font-size:10px;color:#777;text-decoration:underline}
.gallery-card{position:absolute;top:732px;width:199px;height:204px;border:1px solid #e3e3e3;border-bottom:4px solid var(--burgundy);padding:6px}
.gallery-card .photo{height:109px}
.gallery-card p{font-family:Arial,sans-serif;font-size:7.5px;line-height:11.7px;color:var(--muted);margin-top:15px}
.site-footer{position:absolute;top:980px;left:0;width:781px;height:188px;background:var(--dark);color:#fff}
.footer-brand{position:absolute;left:78px;top:18px;display:flex;align-items:center;gap:6px;color:var(--burgundy);font-weight:600}
.footer-brand .brand-sub{color:#fff}
.footer-tag{position:absolute;left:80px;top:71px;width:135px;font-size:8.5px;line-height:11px}
.footer-col h3{font-weight:400;font-size:12px;padding-bottom:3px;border-bottom:2px solid var(--burgundy)}
.footer-col{position:absolute;top:21px;font-size:8.5px;line-height:11px}
.footer-col ul{list-style:none;margin-top:16px}
.map{position:absolute;left:563px;top:58px;width:131px;height:110px;background:linear-gradient(135deg,#e8e6df,#d9d5c8)}
.copyright{position:absolute;top:1168px;left:0;width:781px;height:32px;background:var(--darker);color:#ddd;font-size:7.5px;text-align:center;line-height:32px}
</style>
</head>
<body>
<header class="site-header">
  <div class="brand"><span class="brand-dot"></span><div><span class="brand-name">bluefern</span><span class="brand-sub">Business Services</span></div></div>
  <nav class="main-nav"><a class="active" href="#">Home</a><a href="#">About Us</a><a href="#">Clients</a><a href="#">Services</a><a href="#">Careers</a><a href="#">Contact Us</a></nav>
</header>

<section class="hero" role="img" aria-label="Photo of a smiling man at a laptop holding a glass of red wine in a cafe">
  <div class="hero-caption">
    <h1>Delivering IT Excellence</h1>
    <p>Welcome to Bluefern Business Services, an emerging provider of global IT consulting and software services. We are part of the Marlow Goods group, a family run business and the world's largest multi-channel home delivery wine merchant.</p>
  </div>
</section>

<form class="job-search">
  <div class="field" style="left:23px;width:176px">Keyword<div class="box"><svg width="12" height="12" viewBox="0 0 12 12"><circle cx="6" cy="6" r="4" fill="none" stroke="#aaa" stroke-width="2" stroke-dasharray="2 1.2"/><circle cx="6" cy="6" r="1.5" fill="#aaa"/></svg>Job<svg style="margin-left:auto;margin-right:8px" width="9" height="5" viewBox="0 0 9 5"><path d="M0 0h9L4.5 5z" fill="#666"/></svg></div></div>
  <div class="field" style="left:210px;width:177px">Location<div class="box"><svg width="9" height="12" viewBox="0 0 9 12"><path d="M4.5 11S1 6.5 1 4.3a3.5 3.5 0 017 0C8 6.5 4.5 11 4.5 11z" fill="none" stroke="#999"/><circle cx="4.5" cy="4.3" r="1.2" fill="#999"/></svg>Name of your city or Zipcode</div></div>
  <div class="field" style="left:398px;width:151px">Category<div class="box"><svg width="14" height="12" viewBox="0 0 14 12"><rect x="1" y="3" width="12" height="8" fill="#ccc"/><rect x="3" y="1" width="5" height="3" fill="#bbb"/></svg>Telecommunications</div></div>
  <div class="search-btn"><svg width="11" height="11" viewBox="0 0 11 11"><circle cx="4.5" cy="4.5" r="3.3" fill="none" stroke="#fff" stroke-width="1.5"/><path d="M7 7l3 3" stroke="#fff" stroke-width="1.8"/></svg>Search</div>
</form>

<section class="services">
  <article class="service" style="left:75px">
    <div class="service-icon"><svg width="26" height="24" viewBox="0 0 26 24"><rect x="1" y="1" width="24" height="17" fill="none" stroke="#8a1538" stroke-width="2.5"/><path d="M5 6h10M5 10h14M5 14h8" stroke="#8a1538" stroke-width="1.6"/><path d="M10 18v3h6v-3M7 23h12" stroke="#8a1538" stroke-width="2"/></svg></div>
    <h2>Packaged Applications</h2>
    <p>Lorem Ipsum is simply dummy text of the printing and typesetting industry. Lorem Ipsum has been the industry's standard dummy text ever since the 1500s, when an unknown printer took a galley</p>
    <div class="read-more">Read More</div>
  </article>
  <article class="service" style="left:241px">
    <div class="service-icon"><svg width="28" height="24" viewBox="0 0 28 24"><path d="M14 4C10 1 5 1 2 2v19c3-1 8-1 12 2 4-3 9-3 12-2V2c-3-1-8-1-12 2z" fill="#8a1538"/><path d="M14 4v19" stroke="#fff" stroke-width="1.5"/><path d="M5 7h6M5 11h6M5 15h6M17 7h6M17 11h6M17 15h6" stroke="#fff" stroke-width="1"/></svg></div>
    <h2>Digital Commerce</h2>
    <p>Lorem Ipsum is simply dummy text of the printing and typesetting industry. Lorem Ipsum has been the industry's standard dummy text ever since the 1500s, when an unknown printer took a galley</p>
    <div class="read-more">Read More</div>
  </article>
  <article class="service two-line" style="left:409px">
    <div class="service-icon"><svg width="28" height="28" viewBox="0 0 28 28"><g fill="#8a1538"><circle cx="14" cy="14" r="9"/><rect x="11" y="1" width="6" height="26" rx="1"/><rect x="11" y="1" width="6" height="26" rx="1" transform="rotate(45 14 14)"/><rect x="11" y="1" width="6" height="26" rx="1" transform="rotate(90 14 14)"/><rect x="11" y="1" width="6" height="26" rx="1" transform="rotate(135 14 14)"/></g><circle cx="14" cy="14" r="3.5" fill="#fff"/></svg></div>
    <h2>Enterprises Application Integration</h2>
    <p>Lorem Ipsum is simply dummy text of the printing and typesetting industry. Lorem Ipsum has been the industry's standard dummy text ever since the 1500s,</p>
    <div class="read-more">Read More</div>
  </article>
  <article class="service two-line" style="left:571px">
    <div class="service-icon"><svg width="28" height="28" viewBox="0 0 28 28"><g fill="none" stroke="#8a1538" stroke-width="2"><circle cx="14" cy="14" r="12"/><ellipse cx="14" cy="14" rx="5.5" ry="12"/><path d="M2 14h24M14 2v24M4 8h20M4 20h20"/></g></svg></div>
    <h2>Application Development<br>&amp; Maintenance</h2>
    <p>Lorem Ipsum is simply dummy text of the printing and typesetting industry. Lorem Ipsum has been the industry's standard dummy text ever since the 1500s,</p>
    <div class="read-more">Read More</div>
  </article>
</section>

<h2 class="gallery-title">Our Gallery</h2>
<a class="upload-link" href="#">Upload Picture</a>
<article class="gallery-card" style="left:80px"><div class="photo" role="img" aria-label="Business handshake over a tablet" style="background:linear-gradient(135deg,#2e4a66,#9fb3c6 60%,#dfe6ec)"></div><p>Lorem ipsum dolor sit amet, consectetur adipisicing elit, sed do eiusmod tempor incididunt ut labore et dolore magna aliqua. Ut enim ad minim veniam.</p></article>
<article class="gallery-card" style="left:293px"><div class="photo" role="img" aria-label="Office team reviewing work on a laptop" style="background:linear-gradient(135deg,#e8e8e8,#c9c3bd 50%,#5b5b5b)"></div><p>Lorem ipsum dolor sit amet, consectetur adipisicing elit, sed do eiusmod tempor incididunt ut labore et dolore magna aliqua. Ut enim ad minim veniam.</p></article>
<article class="gallery-card" style="left:507px"><div class="photo" role="img" aria-label="Business meeting around a glass table" style="background:linear-gradient(135deg,#d6dde2,#8c959c 50%,#e6ecef)"></div><p>Lorem ipsum dolor sit amet, consectetur adipisicing elit, sed do eiusmod tempor incididunt ut labore et dolore magna aliqua. Ut enim ad minim veniam.</p></article>

<footer class="site-footer">
  <div class="footer-brand"><span class="brand-dot"></span><div><span class="brand-name">bluefern</span><span class="brand-sub">Business Services</span></div></div>
  <p class="footer-tag">Here at Bluefern Business Services we're always happy to hear from you!</p>
  <div class="footer-col" style="left:251px;width:175px"><h3 style="width:146px">Contact Info</h3>
    <ul><li>Bluefern Business Services Pvt. Ltd.</li><li>6th Floor, Lotus Park Tower II</li><li>Unit C14 Kaveri Industrial Estate</li><li>Guindy</li><li>Chennai, 600099</li><li>Tamil Nadu</li><li style="margin-top:11px">Tel: +91 (44) 55501234</li><li style="margin-top:11px;white-space:nowrap">Email: contactus@bluefernbs-site.com</li></ul></div>
  <div class="footer-col" style="left:441px;width:93px"><h3>Navigation</h3>
    <ul style="padding-left:2px"><li>Home</li><li>About Us</li><li>Clients</li><li>Services</li><li>Careers</li><li>Contact Us</li></ul></div>
  <div class="footer-col" style="left:562px;width:130px"><h3>Find Us</h3></div>
  <div class="map" role="img" aria-label="Street map showing the office location"></div>
</footer>
<div class="copyright">Copyright Bluefern Business Services Private Limited</div>
</body>
</html>
```